Business Card Design - Amberfield Court

We are looking at a new design for our business cards that has a modern and professional look. We run a residential aged care facility focussing on the care of residents. The cards will be used for potential clients, consultants and business opportunities in this sector. Blue and white is our main colours and would to see these colours incorporated in the design.
Industry/Entity Type
Business
Contact Information for Business Card
Amberfield Court, Darren Walsh, dwalsh@amberfieldcourt.com.au, Finance Manager, 0472 639 208, BCom, 37 Marrabel Crescent, Brindle Vale, Qld 4093.
Look and feel
Each slider illustrates characteristics of the customer's brand and the style your logo design should communicate.

```html
<!DOCTYPE html>
<html lang="en">
<head>
<meta charset="utf-8">
<title>Amberfield Court – Business Card</title>
<link rel="stylesheet" href="https://fonts.googleapis.com/css2?family=Source+Sans+3:wght@400;600&display=swap">
<style>
  :root {
    --blue: #4b7995;
    --white: #ffffff;
    --taupe: #a89f98;
    --paper: #f4f4f4;
    --stage: #e9e7e4;
    --muted: #5c6b75;
  }
  * { box-sizing: border-box; margin: 0; padding: 0; }
  html, body {
    width: 1200px; height: 900px; overflow: hidden;
    background: var(--stage);
    font-family: "Source Sans 3", sans-serif;
  }
  .stage { position: relative; width: 1200px; height: 900px; }
  .card {
    position: absolute; top: 291px;
    width: 520px; height: 318px; overflow: hidden;
    box-shadow: 0 6px 18px rgba(0,0,0,0.18);
  }

  /* Front */
  .card--front { left: 50px; background: var(--blue); }
  .front-brand {
    position: absolute; left: 0; right: 0; top: 116px;
    display: flex; justify-content: center; align-items: center; gap: 14px;
    color: var(--white); font-size: 32px; font-weight: 400; line-height: 40px;
    letter-spacing: 4px; text-transform: uppercase; white-space: nowrap;
  }
  .brand-dot { width: 22px; height: 22px; border-radius: 50%; background: currentColor; flex: none; }
  .front-tagline {
    position: absolute; left: 110px; width: 300px; top: 176px;
    background: var(--white); color: var(--blue);
    font-size: 20px; line-height: 30px; text-align: center; white-space: nowrap;
  }

  /* Back */
  .card--back { left: 630px; background: var(--paper); }
  .back-brand {
    position: absolute; left: 0; right: 0; top: 72px;
    display: flex; justify-content: center; align-items: center; gap: 12px;
    color: var(--blue); font-size: 26px; font-weight: 400; line-height: 34px;
    letter-spacing: 3px; text-transform: uppercase; white-space: nowrap;
  }
  .back-brand .brand-dot { width: 20px; height: 20px; }
  .person { position: absolute; left: 330px; top: 124px; color: var(--blue); white-space: nowrap; }
  .person-name { font-size: 19px; font-weight: 600; line-height: 24px; }
  .person-name small { font-size: 12px; font-weight: 600; }
  .person-role { font-size: 13px; line-height: 18px; color: var(--muted); }
  .band {
    position: absolute; left: 0; right: 0; top: 190px; height: 24px;
    background: var(--taupe);
  }
  .back-tagline {
    position: absolute; left: 120px; top: 0;
    color: var(--white); font-size: 16px; line-height: 24px; white-space: nowrap;
  }
  .contact-panel {
    position: absolute; left: 0; right: 0; top: 220px; bottom: 0;
    background: var(--blue); color: var(--white);
  }
  .contact-lines {
    position: absolute; right: 210px; top: 18px;
    text-align: right; font-size: 14px; line-height: 22px; white-space: nowrap;
  }
  .contact-lines .line { display: flex; justify-content: flex-end; align-items: center; gap: 5px; }
  .contact-lines .line--email { margin-top: 10px; font-size: 15px; }
  .contact-lines svg { width: 11px; height: 11px; fill: var(--white); flex: none; }
  .address {
    position: absolute; left: 330px; top: 18px;
    font-size: 13.5px; line-height: 22px; white-space: nowrap;
  }
</style>
</head>
<body>
<main class="stage">
  <section class="card card--front" aria-label="Card front">
    <div class="front-brand"><span class="brand-dot"></span>Amberfield Court</div>
    <div class="front-tagline">Comfort, Respect, Belonging</div>
  </section>

  <section class="card card--back" aria-label="Card back">
    <div class="back-brand"><span class="brand-dot"></span>Amberfield Court</div>
    <div class="person">
      <div class="person-name">Darren Walsh, <small>BCom</small></div>
      <div class="person-role">Finance Manager</div>
    </div>
    <div class="band"><span class="back-tagline">Comfort, Respect, Belonging</span></div>
    <div class="contact-panel">
      <div class="contact-lines">
        <div class="line">0472 639 208
          <svg viewBox="0 0 24 24" aria-hidden="true"><path d="M6.6 10.8a15.1 15.1 0 0 0 6.6 6.6l2.2-2.2c.3-.3.7-.4 1-.2 1.1.4 2.3.6 3.6.6.6 0 1 .4 1 1V20c0 .6-.4 1-1 1A17 17 0 0 1 3 4c0-.6.4-1 1-1h3.5c.6 0 1 .4 1 1 0 1.3.2 2.5.6 3.6.1.3 0 .7-.2 1z"/></svg>
        </div>
        <div class="line line--email">dwalsh@amberfieldcourt.com.au
          <svg viewBox="0 0 24 24" aria-hidden="true"><path d="M2 5h20v14H2zM3.5 6.5 12 13l8.5-6.5z" fill-rule="evenodd"/></svg>
        </div>
      </div>
      <div class="address">37 Marrabel Crescent,<br>Brindle Vale, Qld 4093</div>
    </div>
  </section>
</main>
</body>
</html>
```